Wholesaler needs a bag design for cassava flour

I need design for a package bag to pack cassava flour (white powder). This flower is made from manioc and is very much used by African countries. I want to make packages of 0.5kg with 160mm base to 230mm height. I would like ta package to have clear parts so that customers can see the quality of the product. The brand name of the product is " MAVLO " and the name of the product in Portuguese is "Fuba de Bombó". I want the design to be simple not many colors and attractive.
The design should have a front page and a back page. The front side I would like to have the brand, the name of the product and a simple design while on the back side it should have the space to fill with the nutrition facts, our company information, bar code and other information demanded by EU regulation
Target Market(s)
African Communities in Portugal
Industry/Entity Type
Wholesale

```html
<!DOCTYPE html>
<html lang="en">
<head>
<meta charset="utf-8">
<title>MAVLO Fuba de Bombó – bag front and back</title>
<link href="https://fonts.googleapis.com/css2?family=Crimson+Text:wght@400;600;700&family=Arimo:wght@400;700&family=Archivo+Black&display=swap" rel="stylesheet">
<style>
  :root {
    --stage: #f2f0ec;
    --cream-top: #fdf4e3;
    --cream-mid: #f3e4c8;
    --sand-bottom: #c6a97c;
    --oval: #ecebe7;
    --brand-brown: #6e3a1a;
    --ink: #1c1a18;
    --label-white: #ffffff;
    --root-flesh: #efe4d8;
    --root-skin: #a4604d;
    --root-dark: #864a3b;
    --box-line: #faf5ec;
  }
  * { margin: 0; padding: 0; box-sizing: border-box; }
  html, body { width: 911px; height: 1200px; overflow: hidden; background: var(--stage); }

  .sheet {
    position: absolute;
    left: 20px; top: 292px;
    width: 1594px; height: 1127px;
    transform: scale(0.5464);
    transform-origin: 0 0;
  }
  .panel {
    position: absolute; top: 0;
    width: 791px; height: 1127px;
    overflow: hidden;
    background: linear-gradient(180deg, var(--cream-top) 0%, var(--cream-top) 12%, var(--cream-mid) 55%, var(--sand-bottom) 100%);
  }
  .panel--front { left: 0; }
  .panel--back { left: 803px; }

  /* front */
  .front-art { position: absolute; inset: 0; }
  .brand-name {
    position: absolute; left: 0; right: 0; top: 482px;
    text-align: center;
    font-family: "Crimson Text", serif; font-weight: 600;
    font-size: 96px; line-height: 100px; letter-spacing: 4px;
    color: var(--brand-brown);
  }
  .product-name {
    position: absolute; left: 0; right: 0; top: 925px;
    text-align: center;
    font-family: "Crimson Text", serif; font-weight: 600;
    font-size: 104px; letter-spacing: 1px;
    color: var(--label-white);
    text-shadow: 0 0 2px rgba(40,20,10,.85);
  }

  /* back */
  .back-headline {
    position: absolute; left: 86px; top: 172px; width: 680px;
    font-family: "Crimson Text", serif; font-weight: 400;
    font-size: 45px; line-height: 55px; color: var(--ink);
    white-space: nowrap;
  }
  .nutrition {
    position: absolute; left: 86px; top: 331px; width: 330px; height: 563px;
    background: var(--label-white);
    border: 2px solid var(--ink);
    box-shadow: 3px 3px 0 rgba(0,0,0,.25);
    padding: 8px 14px 0 14px;
    font-family: "Arimo", sans-serif; font-size: 15px; color: var(--ink);
  }
  .nutrition__title { font-family: "Archivo Black", sans-serif; font-size: 35px; line-height: 40px; letter-spacing: .3px; white-space: nowrap; }
  .nutrition__row { display: flex; justify-content: space-between; align-items: flex-end; height: 23.4px; border-top: 1px solid #777; line-height: 18px; white-space: nowrap; }
  .nutrition__row--plain { border-top: none; height: 18px; }
  .nutrition__row--indent span:first-child { padding-left: 25px; }
  .nutrition__row--right { justify-content: flex-end; font-size: 10px; font-weight: 700; }
  .nutrition__bar { height: 10px; background: var(--ink); margin: 6px 0 2px; }
  .nutrition__bar--thin { height: 5px; margin: 6px 0 0; }
  .nutrition b { font-weight: 700; }
  .nutrition__note { border-top: 1px solid #777; font-size: 11px; line-height: 14px; padding-top: 6px; height: 50px; }

  .back-copy {
    position: absolute; left: 440px; top: 400px; width: 340px;
    text-align: center; white-space: nowrap;
    font-family: "Crimson Text", serif; font-weight: 700;
    font-size: 20px; line-height: 25.6px; color: var(--ink);
  }
  .company-info {
    position: absolute; left: 421px; top: 913px; width: 343px; height: 125px;
    border: 1.5px solid var(--box-line);
    text-align: center; padding-top: 8px; white-space: nowrap;
    font-family: "Crimson Text", serif; font-size: 19.5px; line-height: 25px; color: var(--ink);
  }
  .company-info__title { font-weight: 700; }
</style>
</head>
<body>
<main class="sheet">
  <section class="panel panel--front" aria-label="Bag front">
    <svg class="front-art" width="791" height="1127" viewBox="0 0 791 1127">
      <defs>
        <linearGradient id="roots" x1="0" y1="0" x2="0" y2="1">
          <stop offset="0" stop-color="var(--root-flesh)"/>
          <stop offset="0.22" stop-color="var(--root-skin)"/>
          <stop offset="1" stop-color="var(--root-dark)"/>
        </linearGradient>
      </defs>
      <ellipse cx="395" cy="580" rx="350" ry="443" fill="var(--oval)"/>
      <circle class="brand-mark" cx="396" cy="362" r="100" fill="none" stroke="var(--brand-brown)" stroke-width="10"/>
      <path role="img" aria-label="Photo of cut cassava roots"
            d="M0 790 C60 700 200 680 322 692 C360 610 520 592 640 602 C680 530 740 505 791 505 L791 1127 L0 1127 Z"
            fill="url(#roots)"/>
    </svg>
    <div class="brand-name">MAVLO</div>
    <h1 class="product-name">Fuba de Bombó</h1>
  </section>

  <section class="panel panel--back" aria-label="Bag back">
    <p class="back-headline">Lorem ipsum dolor sit amet, con-<br>sectetuer adipiscing elit, sed diam</p>

    <div class="nutrition">
      <div class="nutrition__title">Nutrition Facts</div>
      <div class="nutrition__row nutrition__row--plain"><span>Serving Size</span><span>...g</span></div>
      <div class="nutrition__row nutrition__row--plain"><span>Servings Per Container</span><span></span></div>
      <div class="nutrition__bar"></div>
      <div class="nutrition__row nutrition__row--plain"><span><b>Amount Per Serving</b></span></div>
      <div class="nutrition__row"><span><b>Calories</b> ....</span><span>Calories from Fat ...</span></div>
      <div class="nutrition__row nutrition__row--right"><span>% Daily Value*</span></div>
      <div class="nutrition__row"><span><b>Total Fat</b> ...g</span><b>...%</b></div>
      <div class="nutrition__row nutrition__row--indent"><span>Saturated Fat ...g</span><b>...%</b></div>
      <div class="nutrition__row nutrition__row--indent"><span><i>Trans</i> Fat ...g</span><span></span></div>
      <div class="nutrition__row"><span><b>Cholestrol</b> ...mg</span><b>...%</b></div>
      <div class="nutrition__row"><span><b>Sodium</b> ...mg</span><b>...%</b></div>
      <div class="nutrition__row"><span><b>Total Carbohydrate</b> ...g</span><b>...%</b></div>
      <div class="nutrition__row nutrition__row--indent"><span>Dietary Fiber ...g</span><b>...%</b></div>
      <div class="nutrition__row nutrition__row--indent"><span>Sugars ...g</span><span></span></div>
      <div class="nutrition__row"><span><b>Protein</b> ...g</span><span></span></div>
      <div class="nutrition__bar"></div>
      <div class="nutrition__row nutrition__row--plain"><span>Vitamin A</span><b>...%</b></div>
      <div class="nutrition__row"><span>Vitamin C</span><b>...%</b></div>
      <div class="nutrition__row"><span>Calcium</span><b>...%</b></div>
      <div class="nutrition__row"><span>Iron</span><b>...%</b></div>
      <div class="nutrition__note">*Percent Daily Values are based on a 2,000 calorie diet. Your Daily Values may be higer or lower depending on your calorie needs.</div>
      <div class="nutrition__bar nutrition__bar--thin"></div>
    </div>

    <p class="back-copy">Lorem ipsum dolor sit amet,<br>consectetuer adipiscing elit, sed<br>diam nonummy nibh euismod<br>tincidunt ut laoreet dolore magna<br>aliquam erat volutpat. Ut wisi<br>enim ad minim veniam, quis<br>nostrud exerci tation ullamcorper<br>suscipit lobortis nisl ut aliquip ex<br>ea commodo consequat. Duis<br>autem vel eum iriure dolor in<br>hendrerit in vulputate velit esse<br>molestie consequat, vel illum<br>dolore eu feugiat nulla facilisis at<br>vero eros et accumsan et iusto odio<br>dignissim qui blandit praesent<br>luptatum zzril delenit augue duis<br>dolore te feugait nulla facilisi.<br>Lorem ipsum dolor sit amet, cons</p>

    <div class="company-info">
      <div class="company-info__title">company information</div>
      <div>Lorem ipsum dolor sit amet, consec-<br>tetuer adipiscing elit, sed diam<br>nonummy nibh euismod tincidunt</div>
    </div>
  </section>
</main>
</body>
</html>
```